creation of a business card design for a company specializing in the creation...

I would like to create a design for a professional business card on a black background and with the company's colors (I am attaching some files: including the logo in horizontal and centered format, I am also attaching a recent project design a T-shirt, this is the one I chose to give you an idea of my preferences.

we are in the process of developing a new website design, it is still in the development phase but it can be viewed at the following address: www.vantrelmo.be to give you other ideas about the company
you will see for yourself the subject of my main activity: company specializing in the construction of stairs

I would like a business card that stands out from the rest with a unique design

here is the informations
Name: Lucien Barthel
Function: Manager
Address: Rue Moulinet du Parc 42
7180 La Louvière
telephone: +32 468 219 804
email: info@rx7p.be
website: rx7p. be
social networks: Facebook, YouTube, TikTok, Instagram

Target Market(s)

customer who wants to have a beautiful staircase built

Industry/Entity Type

contruction d'escalier

Contact Information for Business Card

Adresse. Numero de telephone, site web, le texte : "Createur d'escalier", logo recto-verso, icone des reseaux sociaux

Requirements
Must have
• the mention: Stair creator
Nice to have
• an illustration of a designer staircase
Should not have
• do not distort the logo

```html
<!DOCTYPE html>
<html lang="fr">
<head>
<meta charset="utf-8">
<title>RX7P – Business Card</title>
<link href="https://fonts.googleapis.com/css2?family=Open+Sans:wght@400;600;700&display=swap" rel="stylesheet">
<style>
  :root {
    --page-bg: #e9e7e4;
    --card-black: #050505;
    --card-sheen: #1c1c1c;
    --steel-blue: #6f9bbb;
    --steel-blue-dark: #4f7896;
    --ice-blue: #a9c6dc;
    --text-white: #f4f6f8;
  }
  * { box-sizing: border-box; margin: 0; padding: 0; }
  html, body {
    width: 1200px; height: 780px; overflow: hidden;
    background: var(--page-bg);
    font-family: "Open Sans", Arial, sans-serif;
  }
  .canvas {
    position: relative; width: 1200px; height: 780px;
    display: flex; flex-direction: column; align-items: center; justify-content: center; gap: 40px;
  }
  .card {
    position: relative; width: 580px; height: 331px;
    background: linear-gradient(115deg, var(--card-sheen) 0%, var(--card-black) 45%, var(--card-black) 100%);
    border-bottom: 6px solid var(--steel-blue);
    border-radius: 4px;
    box-shadow: 0 10px 24px rgba(0,0,0,.25);
    overflow: hidden;
    color: var(--text-white);
  }
  /* front */
  .card-front { display: flex; flex-direction: column; align-items: center; justify-content: center; }
  .brand-lockup { display: flex; align-items: center; gap: 18px; }
  .brand-dot { width: 22px; height: 22px; border-radius: 50%; background: var(--text-white); }
  .brand-name {
    font-weight: 400; font-size: 92px; line-height: 1; letter-spacing: 6px; color: var(--text-white);
  }
  .brand-tagline {
    margin-top: 14px; font-size: 15px; font-weight: 600; letter-spacing: 9px;
    color: var(--ice-blue); text-transform: uppercase;
  }
  /* back */
  .emblem { position: absolute; left: 30px; top: 14px; width: 200px; height: 196px; }
  .emblem-arc-text { font-family: "Open Sans", Arial, sans-serif; font-size: 11px; font-weight: 700; letter-spacing: 1.5px; fill: var(--text-white); }
  .emblem-name { font-family: "Open Sans", Arial, sans-serif; font-size: 24px; font-weight: 400; letter-spacing: 3px; fill: var(--text-white); }
  .emblem-tagline { font-family: "Open Sans", Arial, sans-serif; font-size: 7.5px; font-weight: 600; letter-spacing: 2.5px; fill: var(--ice-blue); }
  .emblem-contact { font-family: "Open Sans", Arial, sans-serif; font-size: 7px; font-weight: 600; fill: var(--text-white); }
  .holder { position: absolute; left: 34px; top: 214px; display: flex; align-items: baseline; gap: 8px; }
  .holder-name { font-size: 31px; font-weight: 700; color: var(--steel-blue); }
  .holder-role { font-size: 15px; font-weight: 400; color: var(--text-white); }
  .contact-list {
    position: absolute; left: 34px; top: 264px; right: 30px;
    display: grid; grid-template-columns: 1fr 1fr; row-gap: 6px; column-gap: 10px;
    font-size: 14.5px; list-style: none;
  }
  .contact-list .wide { grid-column: 1 / span 2; }
  .contact-label { color: var(--steel-blue); font-weight: 700; margin-right: 6px; }
  .web-line { position: absolute; right: 34px; top: 60px; font-size: 15px; }
</style>
</head>
<body>
<main class="canvas">
  <section class="card card-front" aria-label="Recto">
    <div class="brand-lockup">
      <span class="brand-dot"></span>
      <span class="brand-name">RX7P</span>
    </div>
    <p class="brand-tagline">Original Staircases</p>
  </section>

  <section class="card card-back" aria-label="Verso">
    <svg class="emblem" viewBox="0 0 200 196" aria-label="Emblème Créateur d'escalier">
      <defs>
        <radialGradient id="stair-tone" cx="45%" cy="40%" r="65%">
          <stop offset="0" stop-color="#c9d3db"/>
          <stop offset=".45" stop-color="#7d98ad"/>
          <stop offset="1" stop-color="#24323e"/>
        </radialGradient>
        <path id="emblem-arc" d="M26,80 A74,74 0 0 1 174,80"/>
      </defs>
      <circle cx="100" cy="80" r="62" fill="none" stroke="var(--steel-blue-dark)" stroke-width="5"/>
      <circle cx="100" cy="80" r="56" fill="url(#stair-tone)" role="img" aria-label="Illustration d'un escalier suspendu"/>
      <text class="emblem-arc-text"><textPath href="#emblem-arc" startOffset="50%" text-anchor="middle">CRÉATEUR D'ESCALIER</textPath></text>
      <text class="emblem-name" x="100" y="163" text-anchor="middle">RX7P</text>
      <text class="emblem-tagline" x="100" y="176" text-anchor="middle">ORIGINAL STAIRCASES</text>
      <circle cx="46" cy="187" r="3.5" fill="var(--steel-blue)"/>
      <text class="emblem-contact" x="53" y="189.5">0468 219 804</text>
      <circle cx="111" cy="187" r="3.5" fill="var(--steel-blue)"/>
      <text class="emblem-contact" x="118" y="189.5">RX7P.BE</text>
    </svg>
    <p class="web-line"><span class="contact-label">W:</span>www.rx7p.be</p>
    <p class="holder"><span class="holder-name">Lucien Barthel</span><span class="holder-role">Manager</span></p>
    <ul class="contact-list">
      <li><span class="contact-label">T:</span>+32 468 219 804</li>
      <li><span class="contact-label">E:</span>info@rx7p.be</li>
      <li class="wide"><span class="contact-label">L:</span>Rue Moulinet du Parc 42 7180 La Louvière</li>
    </ul>
  </section>
</main>
</body>
</html>
```